Brookvane Consulting Business Card Design

Business Card Design for Brookvane Consulting. Brookvane Consulting is a boutique consultancy based in Atlanta, GA., that specializes in marketing strategy, organization planning, and leadership development. We provide solutions for small businesses and startups as well as Vantage 300 companies.

http://brookvaneconsulting.com/

Target Market(s)

We provide solutions for small businesses and startups as well as Vantage 300 companies.

Industry/Entity Type

Consulting

Contact Information for Business Card

Two sided business card with priority on contact information, logo, tag line (Inspiration to Dream More, Do More, Become More)

Colors

Designer to choose colors to be used in the design.

Requirements
Must have
• contact information, logo, tag line (Inspiration to Dream More, Do More, Become More)
• Simple no over communication.
Nice to have
• I would like to see different placements of logo and creative use of both sides of the card
Should not have
• Do not put too much information on the card.

```html
<!DOCTYPE html>
<html lang="en">
<head>
<meta charset="utf-8">
<title>Brookvane Consulting Business Card</title>
<link href="https://fonts.googleapis.com/css2?family=Lato:wght@400;700&display=swap" rel="stylesheet">
<style>
  :root {
    --charcoal: #333333;
    --paper: #ffffff;
    --ink: #2b2b2b;
    --backdrop: #e9e7e4;
  }
  * { margin: 0; padding: 0; box-sizing: border-box; }
  html, body {
    width: 1200px; height: 900px; overflow: hidden;
    background: var(--backdrop);
    font-family: 'Lato', sans-serif;
  }
  .canvas { position: relative; width: 1200px; height: 900px; }

  .card { position: absolute; box-shadow: 0 4px 14px rgba(0,0,0,0.18); overflow: hidden; }

  /* Front card */
  .card-front { left: 78px; top: 35px; width: 587px; height: 362px; background: var(--paper); }
  .brand-band {
    position: absolute; left: 0; top: 0; width: 172px; height: 100%;
    background: var(--charcoal);
  }
  .brand-band .brand-name {
    position: absolute; left: 86px; top: 181px;
    transform: translate(-50%, -50%) rotate(-90deg);
    white-space: nowrap;
    color: var(--paper); font-weight: 400; font-size: 30px; letter-spacing: 1px;
  }
  .contact-block { position: absolute; left: 217px; top: 108px; color: var(--ink); }
  .person-name { font-size: 21px; font-weight: 700; letter-spacing: 0.3px; line-height: 1.1; }
  .person-role { font-size: 16px; font-weight: 400; margin-top: 2px; }
  .contact-list { list-style: none; margin-top: 40px; font-size: 16px; line-height: 22px; }
  .contact-list li { display: flex; align-items: center; gap: 6px; }
  .contact-list svg { width: 13px; height: 13px; fill: var(--ink); flex: none; }

  /* Back card */
  .card-back { left: 389px; top: 505px; width: 566px; height: 352px; background: var(--charcoal); }
  .card-back .brand-name {
    position: absolute; left: 0; right: 0; top: 132px; text-align: center;
    color: var(--paper); font-weight: 400; font-size: 42px; letter-spacing: 1px;
  }
  .arrow-rule { position: absolute; left: 77px; top: 268px; width: 414px; height: 20px; }
  .tagline {
    position: absolute; left: 0; right: 0; top: 298px; text-align: center;
    color: var(--paper); font-size: 14.5px; font-weight: 700; text-transform: uppercase; letter-spacing: 0.2px;
  }
</style>
</head>
<body>
<main class="canvas">
  <section class="card card-front" aria-label="Business card front">
    <div class="brand-band">
      <span class="brand-name">Brookvane Consulting</span>
    </div>
    <div class="contact-block">
      <h1 class="person-name">DANIEL HARPER</h1>
      <p class="person-role">Managing Director</p>
      <ul class="contact-list">
        <li><svg viewBox="0 0 16 16" aria-hidden="true"><path d="M2 5c0-2 2-3 6-3s6 1 6 3v1h-3V5H5v1H2zM4 7h8l2 7H2z"/></svg>404 555 0172</li>
        <li><svg viewBox="0 0 16 16" aria-hidden="true"><path d="M1 3h14v10H1zM2 4l6 5 6-5v1L8 10 2 5z" fill-rule="evenodd"/></svg>hello@brookvanemail.com</li>
        <li><svg viewBox="0 0 16 16" aria-hidden="true"><circle cx="8" cy="8" r="7"/><path d="M1 8h14M8 1c-3 3-3 11 0 14M8 1c3 3 3 11 0 14" stroke="#fff" stroke-width="1" fill="none"/></svg>www.brookvaneconsulting.com</li>
      </ul>
    </div>
  </section>

  <section class="card card-back" aria-label="Business card back">
    <div class="brand-name">Brookvane Consulting</div>
    <svg class="arrow-rule" viewBox="0 0 414 20" aria-hidden="true">
      <line x1="0" y1="10" x2="400" y2="10" stroke="#fff" stroke-width="1"/>
      <path d="M390 2 L412 10 L390 18 L396 10 Z" fill="none" stroke="#fff" stroke-width="1.2"/>
    </svg>
    <p class="tagline">Inspiration to dream more, do more, become more</p>
  </section>
</main>
</body>
</html>
```